New design for Giftwell Hub Website - landing page plus 3 carousel pages

We have a new website we want to launch for 501c3 organizations - Faith-based organizations, not for profit organizations, colleges and universities. Note - this is a design only project. We want to see designs for the landing page and the 3 other pages - Faith-based organizations, not for profit organizations, colleges and universities.
Format: We expect to create this website in Wix so requirement is to make the graphics Wix compatible
See Dossier attached for more details, 4 wireframes (1 landing page and 3 carousel pages), and brand guidelines
Please be creative and and make the visuals engaging. We do NOT want you to simply replicate what is in the wireframe. We are looking for a totally new, fresh and engaging design.
Number of Pages Required
1 page
Look and feel
Each slider illustrates characteristics of the customer's brand and the style your logo design should communicate.

```html
<!DOCTYPE html>
<html lang="en">
<head>
<meta charset="utf-8">
<title>Giftwell Hub – 501 C3 Organization</title>
<link rel="stylesheet" href="https://fonts.googleapis.com/css2?family=Lexend:wght@300;400&family=Roboto:wght@400;500;700&display=swap">
<style>
:root{
  --navy:#1c1a3a;
  --navy-deep:#0f1b32;
  --green:#00bd91;
  --green-dark:#00a07c;
  --white:#ffffff;
  --ink:#1d1d1d;
  --grey:#6d6d6d;
  --line:#dcdcdc;
}
*{box-sizing:border-box;margin:0;padding:0}
html,body{width:1200px;height:4052px;overflow:hidden}
body{position:relative;font-family:Roboto,Arial,sans-serif;color:var(--ink);background:var(--white)}
.abs{position:absolute}
.center{left:0;width:1200px;text-align:center}
.btn{position:absolute;display:flex;align-items:center;justify-content:center;gap:10px;font:700 13px Roboto,sans-serif;color:var(--white);letter-spacing:.2px}
.btn .dot{width:13px;height:13px;border-radius:50%;background:var(--white);position:relative}
.btn .dot::after{content:"";position:absolute;left:5px;top:3.5px;border-left:4px solid var(--navy);border-top:3px solid transparent;border-bottom:3px solid transparent}
.light-head{font-family:Lexend,sans-serif;font-weight:300}

/* header */
.site-header{top:0;left:0;width:1200px;height:75px;background:var(--navy);z-index:3}
.brand{position:absolute;display:flex;align-items:center;gap:10px;color:var(--white);font:500 20px Roboto,sans-serif}
.brand .mark{width:44px;height:44px;border-radius:50%;border:3px solid var(--white)}
.nav{position:absolute;left:457px;top:30px;display:flex;gap:32px;font:700 11.5px Roboto,sans-serif;color:var(--white)}
.login{left:997px;top:21px;width:92px;height:34px;border:1.5px solid var(--white);border-radius:3px;font-size:11.5px}

/* hero */
.hero-bg{top:0;left:0;width:1200px;height:720px}
.hero-title{top:218px;font:300 64px Lexend,sans-serif;color:var(--white)}
.hero-text{top:320px;font:700 19.5px/29px Roboto,sans-serif;color:var(--white)}
.orb{position:absolute;width:324px;height:324px;border-radius:50%;display:flex;align-items:center;justify-content:center}
.orb .ring{position:absolute;inset:16px;border-radius:50%;border:3px solid var(--white)}
.orb.green{background:var(--green)}
.orb.dark{background:var(--navy-deep)}
.orb .icon{position:absolute;top:62px;left:50%;transform:translateX(-50%);width:110px;height:110px;border-radius:50%}
.orb .label{position:absolute;top:190px;width:100%;text-align:center;font:700 30px/34px Roboto,sans-serif;color:var(--white)}

/* process */
.section-title{font:300 36px Lexend,sans-serif;color:var(--ink)}
.step{position:absolute;left:647px;width:420px}
.step h3{font:700 17.5px Roboto,sans-serif;color:var(--ink)}
.step .rule{width:32px;height:2px;background:var(--green);margin:14px 0 12px}
.step p{font:400 13.5px/20px Roboto,sans-serif;color:var(--grey)}
.donate-data{left:515px;top:1562px;width:170px;height:50px;background:var(--navy-deep);border-radius:3px}

/* donation */
.donation{top:1672px;left:0;width:1200px;height:404px;background:var(--green)}
.donation h2{top:60px;font:300 36px Lexend,sans-serif;color:var(--white)}
.donation .sub{top:118px;font:700 20px Roboto,sans-serif;color:var(--white)}
.give-label{left:110px;top:200px;font:700 24px Roboto,sans-serif;color:var(--white)}
.amount{position:absolute;top:188px;width:123px;height:52px;border:2px solid var(--white);display:flex;align-items:center;justify-content:center;font:700 24px Roboto,sans-serif;color:var(--white)}
.amount.other{background:var(--navy-deep);border-color:var(--navy-deep);font-size:13.5px;width:124px}
.card-btn{left:310px;top:289px;width:255px;height:49px;background:var(--navy-deep);border-radius:3px}
.pay-row{position:absolute;left:587px;top:298px;display:flex;gap:4px}
.pay-row span{display:flex;align-items:center;justify-content:center;height:30px;padding:0 6px;background:var(--white);border-radius:3px;font:700 11px Roboto,sans-serif;color:var(--navy-deep)}

/* ways to give */
.give-card{position:absolute;top:2163px;width:475px;height:176px;border-radius:88px;background:var(--white);box-shadow:0 6px 18px rgba(0,0,0,.18)}
.give-card .badge{position:absolute;left:24px;top:18px;width:140px;height:140px;border-radius:50%}
.give-card h3{position:absolute;left:194px;top:40px;font:500 25px Roboto,sans-serif;color:var(--ink)}
.give-card .btn{left:196px;top:90px;width:124px;height:42px;font-size:13px}

/* enroll */
.enroll{top:2581px;left:0;width:1200px;height:568px;background:var(--navy)}
.video{left:311px;top:2415px;width:579px;height:361px;border:4px solid var(--white);box-shadow:0 4px 14px rgba(0,0,0,.35);background:linear-gradient(120deg,#1a3b52 0%,#20324a 55%,#2b2f5a 100%)}
.play{position:absolute;left:50%;top:50%;width:48px;height:48px;margin:-24px 0 0 -24px;border-radius:50%;background:var(--green)}
.play::after{content:"";position:absolute;left:19px;top:15px;border-left:14px solid var(--white);border-top:9px solid transparent;border-bottom:9px solid transparent}
.enroll-title{top:2827px;font:300 36px Lexend,sans-serif;color:var(--white)}
.enroll-sub{top:2890px;font:700 19px Roboto,sans-serif;color:var(--white)}
.feature{position:absolute;top:2971px}
.feature .circle{position:absolute;left:0;top:0;width:104px;height:104px;border-radius:50%;background:var(--green);display:flex;align-items:center;justify-content:center}
.feature h4{position:absolute;left:121px;top:15px;font:700 20px Roboto,sans-serif;color:var(--white);white-space:nowrap}
.feature p{position:absolute;left:122px;top:48px;width:200px;font:400 13px/21px Roboto,sans-serif;color:var(--white)}

/* newsletter */
.notify-title{top:3210px;font:300 33px Lexend,sans-serif;color:var(--ink)}
.never{top:3270px;font:700 24px Roboto,sans-serif;color:var(--green)}
.subscribe-line{top:3315px;font:400 20px Roboto,sans-serif;color:#444}
.notify-text{top:3368px;left:110px;width:980px;text-align:center;font:400 14.5px/26px Roboto,sans-serif;color:var(--grey)}
.email{left:276px;top:3436px;width:443px;height:50px;border:1px solid var(--line);border-radius:3px;display:flex;align-items:center;padding:0 20px;font:400 14px Roboto,sans-serif;color:#777;justify-content:space-between}
.subscribe-btn{left:730px;top:3436px;width:194px;height:50px;background:var(--green);border-radius:3px;font-size:14px}

/* footer */
.site-footer{top:3575px;left:0;width:1200px;height:420px;background:var(--navy)}
.contact{position:absolute;top:85px;display:flex;align-items:center;gap:18px;color:var(--white);font:400 14px/20px Roboto,sans-serif}
.contact .ic{width:42px;height:42px;border-radius:50%;background:var(--green);flex:none;display:flex;align-items:center;justify-content:center}
.divider{left:110px;top:150px;width:978px;height:1px;background:rgba(255,255,255,.25)}
.foot-brand{left:112px;top:195px;font:500 34px Roboto,sans-serif}
.foot-brand .mark{width:62px;height:62px}
.foot-about{left:112px;top:292px;width:318px;font:400 13px/22px Roboto,sans-serif;color:var(--white);text-align:justify}
.col{position:absolute;top:190px;color:var(--white)}
.col h5{font:700 16px Roboto,sans-serif;text-decoration:underline;margin-bottom:18px}
.col li{list-style:none;font:400 14px Roboto,sans-serif;height:34.5px;display:flex;align-items:center;gap:14px}
.col li::before{content:"»";font-size:14px}
.col.social li::before{content:"";width:11px;height:11px;border-radius:50%;background:var(--white)}
.copyright{top:3995px;left:0;width:1200px;height:57px;background:var(--green);display:flex;align-items:center;justify-content:center;font:400 15px Roboto,sans-serif;color:var(--white)}
</style>
</head>
<body>

<!-- header -->
<header class="abs site-header">
  <div class="brand" style="left:112px;top:14px"><span class="mark"></span>Giftwell Hub</div>
  <nav class="nav">
    <span>ABOUT US ▾</span><span>NEWSROOM</span><span>PATENTS</span><span>CLIENTS</span><span>FAQ</span><span>CONTACT</span>
  </nav>
  <div class="btn login">LOG IN</div>
</header>

<!-- hero -->
<svg class="abs hero-bg" viewBox="0 0 1200 720" role="img" aria-label="Photo of many joined hands, tinted dark navy">
  <defs>
    <linearGradient id="heroShade" x1="0" y1="0" x2="0" y2="1">
      <stop offset="0" stop-color="#3c3a58"/><stop offset="1" stop-color="#1c1a3a"/>
    </linearGradient>
  </defs>
  <path d="M0 0H1200V590Q600 760 0 570Z" fill="url(#heroShade)"/>
</svg>
<h1 class="abs center hero-title">501 C3 Organization</h1>
<p class="abs center hero-text">Lorem ipsum dolor sit amet, consectetur adipiscing elit, sed do eiusmod tempor incididunt<br>ut labore et dolore magna aliqua Ut enim ad minim veniam quis nostrud</p>

<div class="orb green" style="left:110px;top:491px">
  <span class="ring"></span>
  <span class="icon" role="img" aria-label="Emblem of linked figures" style="background:rgba(255,255,255,.85)"></span>
  <span class="label">Non Profit<br>Organization</span>
</div>
<div class="orb dark" style="left:438px;top:491px">
  <span class="ring"></span>
  <span class="icon" role="img" aria-label="Wheel of faith symbols" style="background:var(--green);width:124px;height:124px;top:56px"></span>
  <span class="label" style="top:210px">Faith Base</span>
</div>
<div class="orb green" style="left:764px;top:491px">
  <span class="ring"></span>
  <span class="icon" role="img" aria-label="Graduate figure icon" style="background:rgba(255,255,255,.85)"></span>
  <span class="label">Colleges and<br>Universities</span>
</div>

<!-- process -->
<h2 class="abs center section-title" style="top:872px">Our Process</h2>
<svg class="abs" style="left:0;top:900px" width="640" height="640" viewBox="0 0 640 640">
  <g stroke="#dddddd" stroke-width="2">
    <line x1="260" y1="100" x2="602" y2="100"/><line x1="430" y1="249" x2="602" y2="249"/>
    <line x1="260" y1="398" x2="602" y2="398"/><line x1="430" y1="546" x2="602" y2="546"/>
  </g>
  <g fill="#cfcfcf"><circle cx="602" cy="100" r="7"/><circle cx="602" cy="249" r="7"/><circle cx="602" cy="398" r="7"/><circle cx="602" cy="546" r="7"/></g>
  <g stroke-width="24" stroke-linecap="butt">
    <line x1="240" y1="115" x2="370" y2="235" stroke="var(--green-dark)"/>
    <line x1="370" y1="265" x2="240" y2="385" stroke="var(--navy-deep)"/>
    <line x1="240" y1="412" x2="370" y2="532" stroke="var(--green-dark)"/>
  </g>
  <g font-family="Roboto, sans-serif" font-weight="700" font-size="50" text-anchor="middle" fill="#fff">
    <g transform="translate(225 100)"><rect x="-54" y="-54" width="108" height="108" transform="rotate(45)" fill="var(--green)"/><rect x="-44" y="-44" width="88" height="88" transform="rotate(45)" fill="none" stroke="#fff" stroke-width="3"/><text y="18">01</text></g>
    <g transform="translate(388 249)"><rect x="-54" y="-54" width="108" height="108" transform="rotate(45)" fill="var(--navy-deep)"/><rect x="-44" y="-44" width="88" height="88" transform="rotate(45)" fill="none" stroke="#fff" stroke-width="3"/><text y="18">02</text></g>
    <g transform="translate(225 398)"><rect x="-54" y="-54" width="108" height="108" transform="rotate(45)" fill="var(--green)"/><rect x="-44" y="-44" width="88" height="88" transform="rotate(45)" fill="none" stroke="#fff" stroke-width="3"/><text y="18">03</text></g>
    <g transform="translate(388 546)"><rect x="-54" y="-54" width="108" height="108" transform="rotate(45)" fill="var(--navy-deep)"/><rect x="-44" y="-44" width="88" height="88" transform="rotate(45)" fill="none" stroke="#fff" stroke-width="3"/><text y="18">04</text></g>
  </g>
</svg>
<div class="step" style="top:957px"><h3>Lorem ipsum dolor sit amet, consectetur</h3><div class="rule"></div><p>Sed ut perspiciatis unde omnis iste natus error sit voluptatem accusantium doloremque laudantium, totam</p></div>
<div class="step" style="top:1106px"><h3>Lorem ipsum dolor sit amet, consectetur</h3><div class="rule" style="background:var(--navy-deep)"></div><p>Sed ut perspiciatis unde omnis iste natus error sit voluptatem accusantium doloremque laudantium, totam</p></div>
<div class="step" style="top:1255px"><h3>Lorem ipsum dolor sit amet, consectetur</h3><div class="rule"></div><p>Sed ut perspiciatis unde omnis iste natus error sit voluptatem accusantium doloremque laudantium, totam</p></div>
<div class="step" style="top:1404px"><h3>Lorem ipsum dolor sit amet, consectetur</h3><div class="rule" style="background:var(--navy-deep)"></div><p>Sed ut perspiciatis unde omnis iste natus error sit voluptatem accusantium doloremque laudantium, totam</p></div>
<div class="btn donate-data">DONATE DATA <span class="dot"></span></div>

<!-- donation -->
<section class="abs donation">
  <h2 class="abs center" style="top:60px;font:300 36px Lexend,sans-serif;color:var(--white)">My Donation</h2>
  <p class="abs center sub">All Donations are tax Deductible</p>
  <div class="abs give-label">I want to Give</div>
  <div class="amount" style="left:296px">$25</div>
  <div class="amount" style="left:429px">$50</div>
  <div class="amount" style="left:563px">$100</div>
  <div class="amount" style="left:697px">$125</div>
  <div class="amount" style="left:831px">$150</div>
  <div class="amount other" style="left:964px">Other Amount</div>
  <div class="btn card-btn">DONATE WITH CREDIT CARD <span class="dot"></span></div>
  <div class="pay-row"><span>Veyra</span><span>Mintcard</span><span>Discern</span><span>Amberpay</span><span>PayLoop</span></div>
</section>

<!-- ways to give -->
<div class="give-card" style="left:110px">
  <div class="badge" style="background:var(--navy-deep)">
    <svg width="140" height="140" viewBox="0 0 140 140"><g fill="none" stroke="#fff" stroke-width="3"><circle cx="70" cy="70" r="24"/><path d="M70 30v16M70 94v16M30 70h16M94 70h16M42 42l11 11M87 87l11 11M98 42 87 53M53 87 42 98"/></g></svg>
  </div>
  <h3>Donate with Crypto</h3>
  <div class="btn" style="background:var(--navy-deep)">DONATE <span class="dot"></span></div>
</div>
<div class="give-card" style="left:610px">
  <div class="badge" style="background:var(--green)">
    <svg width="140" height="140" viewBox="0 0 140 140"><g fill="none" stroke="#fff" stroke-width="3"><ellipse cx="70" cy="46" rx="24" ry="8"/><path d="M46 46v48c0 4 11 8 24 8s24-4 24-8V46M46 62c0 4 11 8 24 8s24-4 24-8M46 78c0 4 11 8 24 8s24-4 24-8"/></g></svg>
  </div>
  <h3>Donate with Data</h3>
  <div class="btn" style="background:var(--green)">DONATE <span class="dot"></span></div>
</div>

<!-- enroll -->
<section class="abs enroll"></section>
<div class="abs video" role="img" aria-label="News video still: a studio broadcast with an app feature graphic">
  <span class="play"></span>
</div>
<h2 class="abs center enroll-title">Why Enroll !</h2>
<p class="abs center enroll-sub">To get full access to all the features , start by creating an account</p>

<div class="feature" style="left:110px">
  <div class="circle"><svg width="54" height="54" viewBox="0 0 54 54"><rect x="4" y="8" width="46" height="42" rx="5" fill="#fff"/><g fill="var(--green)"><rect x="11" y="20" width="7" height="7"/><rect x="23" y="20" width="7" height="7"/><rect x="35" y="20" width="7" height="7"/><rect x="11" y="33" width="7" height="7"/><rect x="23" y="33" width="7" height="7"/><rect x="35" y="33" width="7" height="7"/></g></svg></div>
  <h4>Drops</h4><p>Purchase NFTs that are directly sold by top creators</p>
</div>
<div class="feature" style="left:448px">
  <div class="circle"><svg width="58" height="54" viewBox="0 0 58 54"><path d="M6 4h46l4 14H2z" fill="#fff"/><rect x="6" y="22" width="46" height="30" fill="#fff"/><rect x="22" y="32" width="14" height="20" fill="var(--green)"/></svg></div>
  <h4>Marketplace</h4><p>Purchase NFTs that are directly sold by top creators</p>
</div>
<div class="feature" style="left:786px">
  <div class="circle"><svg width="62" height="62" viewBox="0 0 62 62"><g fill="none" stroke="#fff" stroke-width="3"><circle cx="31" cy="31" r="17"/><path d="M31 4v10M31 48v10M4 31h10M48 31h10"/></g><text x="31" y="36" text-anchor="middle" font-family="Roboto, sans-serif" font-weight="700" font-size="13" fill="#fff">NFT</text></svg></div>
  <h4>My NFTs</h4><p>Purchase NFTs that are directly sold by top creators</p>
</div>

<!-- newsletter -->
<h2 class="abs center notify-title">Get Notified About New Amazing Products</h2>
<p class="abs center never">Never Miss a Drop</p>
<p class="abs center subscribe-line">Subscribe for the latest news , drops &amp; Collectibles</p>
<p class="abs notify-text">Sed ut perspiciatis unde omnis iste natus error sit voluptatem accusantium doloremque laudantium, totam rem aperiam, eaque ipsa quae ab illo inventore veritatis et quasi architecto beatae vitae dicta sunt explicabo.</p>
<div class="abs email">Email Address
  <svg width="14" height="11" viewBox="0 0 14 11"><rect width="14" height="11" rx="1" fill="#555"/><path d="M1 1l6 5 6-5" fill="none" stroke="#fff" stroke-width="1.3"/></svg>
</div>
<div class="btn subscribe-btn">SUBSCRIBE NOW</div>

<!-- footer -->
<footer class="abs site-footer">
  <div class="contact" style="left:112px">
    <span class="ic"><svg width="18" height="14" viewBox="0 0 18 14"><rect x="1" y="1" width="16" height="12" fill="none" stroke="#fff" stroke-width="1.8"/><path d="M1 1l8 6 8-6" fill="none" stroke="#fff" stroke-width="1.8"/></svg></span>info@giftwellhub.com</div>
  <div class="contact" style="left:359px">
    <span class="ic"><svg width="16" height="18" viewBox="0 0 16 18"><rect x="1" y="5" width="14" height="12" rx="2" fill="#fff"/><rect x="4" y="1" width="4" height="6" fill="#fff"/></svg></span>+ 1 999 999 9999</div>
  <div class="contact" style="left:591px">
    <span class="ic"><svg width="18" height="18" viewBox="0 0 18 18"><path d="M4 1l3 4-2 2c1 3 3 5 6 6l2-2 4 3-2 3C8 17 1 10 1 3z" fill="#fff"/></svg></span>+ 1 999 999 9999</div>
  <div class="contact" style="left:825px">
    <span class="ic"><svg width="14" height="19" viewBox="0 0 14 19"><path d="M7 1a6 6 0 0 1 6 6c0 5-6 11-6 11S1 12 1 7a6 6 0 0 1 6-6z" fill="#fff"/><circle cx="7" cy="7" r="2.3" fill="var(--green)"/></svg></span>145 , Lorem Ipsum Dolor Amet<br>United States</div>
  <div class="abs divider"></div>
  <div class="brand foot-brand"><span class="mark"></span>Giftwell Hub</div>
  <p class="abs foot-about">We alone can provide you with real-time valuation of your datasets, and allow for their exchange and speculation.</p>
  <div class="col" style="left:489px"><h5>Quick Links</h5><ul><li>Home</li><li>Newsroom</li><li>About us</li><li>Contact</li><li>Resources</li></ul></div>
  <div class="col" style="left:719px"><h5>Other Links</h5><ul><li>FAQ</li><li>Patents</li><li>Terms Of Service</li><li>Privacy Policy</li><li>Contact Us</li></ul></div>
  <div class="col social" style="left:981px"><h5>Follow Us On</h5><ul><li>Friendline</li><li>Chirper</li><li>Pinboard</li><li>Snapgram</li><li>Vidstream</li></ul></div>
</footer>
<div class="abs copyright">© 2022 Giftwell Hub. All Rights Reserved</div>

</body>
</html>
```